NZ First of it's kind solutions directory and marketplace for busy Mums needs a business card design

We need a business card design for our new nationwide business in NZ (long term plans to go global). We provide solutions to the everyday challenges that busy Mums face by connecting them with quality communities and suppliers of carefully selected, relevant products and services. We sell direct via our online marketplace. The final design should communicate our values of inclusivity, quality and smart solutions. Colours should incorporate our logo colour palette of #477077 and #6ba8b2. Our website is at https://www.brightnestmums.example

Target Market(s)

busy Mums, Age 28 – 50, female, income over $100K, location main centres NZ primarily but NZ wide. Is likely juggling work or career with a young family. Probably had hobbies which have fallen by the wayside.
-Wants to succeed in her chosen career without compromising on family life
-to successfully juggle her career without feeling like she is compromising her children
- Is time poor, something always has to give and it’s generally her health (she’ll stay up late, get stressed)
- probably ex corporate or professional career. Has discretional income

Industry/Entity Type

Business

Contact Information for Business Card

Lena Forbisher, Founder, BrightNestMums.example (Strapline Tap; Gather; Sorted), 47 Kowhai Terrace, Ellerslie, Auckland 1051, New Zealand. Mob: 021 483 517 Ph: +64 (0)9 571 4860

Font styles to use
Other font styles liked:
• Raleway, and/or Architects Daughter

Colors
00a990
33b8a4
86cfc6
cfeae6

Requirements
Must have
• the above details, streamline. the logo and colours associated with those logos
Should not have
• foil or metallic colours

```html
<!DOCTYPE html>
<html lang="en">
<head>
<meta charset="utf-8">
<title>BrightNestMums – Business Card</title>
<link href="https://fonts.googleapis.com/css2?family=Raleway:wght@400;500;700;800&display=swap" rel="stylesheet">
<style>
  :root {
    --teal-dark: #477077;
    --teal-light: #6ba8b2;
    --paper: #ffffff;
    --ink: #4a4a4a;
    --backdrop: #2b2b2b;
  }
  * { margin: 0; padding: 0; box-sizing: border-box; }
  html, body { width: 1189px; height: 1200px; overflow: hidden; }
  body { background: var(--backdrop); font-family: 'Raleway', sans-serif; position: relative; }

  .card { position: absolute; left: 171px; width: 856px; height: 489px; overflow: hidden; }
  .card-front { top: 67px; background: var(--teal-dark); }
  .card-back { top: 626px; background: var(--paper); }

  .brand { display: flex; align-items: center; gap: 14px; }
  .brand-dot { width: 22px; height: 22px; border-radius: 50%; flex: none; }
  .brand-name { font-weight: 800; letter-spacing: -0.5px; line-height: 1; }

  .front-brand { position: absolute; left: 0; right: 0; top: 208px; justify-content: center; }
  .front-brand .brand-dot { background: var(--paper); }
  .front-brand .brand-name { color: var(--paper); font-size: 56px; }
  .front-web { position: absolute; left: 0; right: 0; top: 352px; text-align: center;
    color: var(--paper); font-size: 19px; letter-spacing: 2.5px; }
  .front-web strong { font-weight: 700; }

  .back-art { position: absolute; inset: 0; }
  .back-brand { position: absolute; left: 41px; top: 92px; }
  .back-brand .brand-dot { background: var(--teal-dark); }
  .back-brand .brand-name { color: var(--teal-dark); font-size: 46px; }

  .person { position: absolute; left: 41px; top: 218px; }
  .person-name { font-size: 27px; font-weight: 700; line-height: 1; letter-spacing: -0.5px; }
  .person-name .first { color: var(--teal-dark); }
  .person-name .last { color: var(--teal-light); }
  .person-role { font-size: 21px; color: var(--ink); margin-top: 2px; }

  .address { position: absolute; left: 41px; top: 293px; font-size: 20px; line-height: 26px; color: var(--ink); }
  .contacts { position: absolute; left: 41px; top: 382px; list-style: none; font-size: 20px; color: var(--ink); }
  .contacts li { display: flex; align-items: center; gap: 7px; height: 27px; }
  .contacts svg { width: 22px; height: 22px; flex: none; }
</style>
</head>
<body>

<section class="card card-front">
  <div class="brand front-brand">
    <span class="brand-dot"></span>
    <span class="brand-name">BrightNestMums</span>
  </div>
  <p class="front-web">www.<strong>brightnestmums</strong>.example</p>
</section>

<section class="card card-back">
  <svg class="back-art" viewBox="0 0 856 489" preserveAspectRatio="none" aria-hidden="true">
    <rect width="856" height="489" fill="var(--teal-dark)"/>
    <path d="M0 0 H690 Q800 150 765 262 Q735 390 680 489 H0 Z" fill="var(--paper)"/>
    <path d="M514 489 Q700 425 760 228 Q750 385 670 489 Z" fill="var(--teal-light)"/>
  </svg>

  <div class="brand back-brand">
    <span class="brand-dot"></span>
    <span class="brand-name">BrightNestMums</span>
  </div>

  <div class="person">
    <p class="person-name"><span class="first">Lena</span> <span class="last">Forbisher</span></p>
    <p class="person-role">Founder</p>
  </div>

  <address class="address" style="font-style:normal">
    47 Kowhai Terrace,<br>
    Ellerslie, Auckland 1051<br>
    New Zealand
  </address>

  <ul class="contacts">
    <li>
      <svg viewBox="0 0 22 22"><circle cx="11" cy="11" r="10" fill="none" stroke="var(--teal-light)" stroke-width="1.4"/><rect x="7.5" y="5" width="7" height="12" rx="1.2" fill="none" stroke="var(--teal-light)" stroke-width="1.4"/></svg>
      021 483 517
    </li>
    <li>
      <svg viewBox="0 0 22 22"><circle cx="11" cy="11" r="10" fill="none" stroke="var(--teal-light)" stroke-width="1.4"/><path d="M5.5 9.5 Q11 5 16.5 9.5 L15 11 L13 10 L13 9 Q11 8 9 9 L9 10 L7 11 Z M7 12 H15 L16 16 H6 Z" fill="var(--teal-light)"/></svg>
      +64 (0)9 571 4860
    </li>
    <li>
      <svg viewBox="0 0 22 22"><circle cx="11" cy="11" r="10" fill="none" stroke="var(--teal-light)" stroke-width="1.4"/><circle cx="11" cy="11" r="6" fill="none" stroke="var(--teal-light)" stroke-width="1.2"/><path d="M5 11 H17 M11 5 V17 M11 5 Q7 11 11 17 M11 5 Q15 11 11 17" fill="none" stroke="var(--teal-light)" stroke-width="1"/></svg>
      www.brightnestmums.example
    </li>
  </ul>
</section>

</body>
</html>
```